Harborline Family Counsel Billboard

We are looking for a billboard design for a Florida divorce law firm. We are unique in the legal field for offering flat fee pricing. Other law firms are expensive, charging hourly rates. We have A LOT of lawyers advertising for personal injury, so we are looking for something fun that will catch the attention and drive home the message that we are an affordable firm to hire for their divorce because we charge a fixed fee. We want people to be directed to steadyratesplit.com

Target Market(s)

Individual seeking a fast and affordable divorce at a fixed fee instead of hourly

Industry/Entity Type

Legal

Requirements
Must have
• Name of firm, logo, steadyratesplit.com, and in small font: Main Office Jacksonville
Should not have
• Promises. Price

```html
<!DOCTYPE html>
<html lang="en">
<head>
<meta charset="utf-8">
<title>Harborline Family Counsel Billboard</title>
<link rel="stylesheet" href="https://fonts.googleapis.com/css2?family=Bebas+Neue&family=Poppins:wght@300;400;500;600;700&display=swap">
<style>
  :root {
    --navy: #1f4366;
    --gold: #a8801c;
    --white: #ffffff;
    --ink: #111111;
    --page: #e8e8e8;
    --photo-light: #d9d4cf;
    --photo-dark: #2a2c33;
  }
  * { margin: 0; padding: 0; box-sizing: border-box; }
  html, body { width: 960px; height: 1200px; overflow: hidden; }
  body { background: var(--page); position: relative; font-family: "Poppins", sans-serif; }

  .billboard {
    position: absolute; left: 30px; top: 469px;
    width: 900px; height: 262px;
    background: var(--white);
    overflow: hidden;
    box-shadow: 0 14px 40px rgba(0,0,0,0.28);
  }
  .billboard__shapes { position: absolute; inset: 0; }

  .brand {
    position: absolute; left: 24px; top: 36px; width: 184px;
    text-align: center; color: var(--white);
  }
  .brand__dot {
    width: 56px; height: 56px; border-radius: 50%;
    background: var(--gold); margin: 0 auto 10px;
  }
  .brand__name {
    font-weight: 500; font-size: 17px; line-height: 1.15; letter-spacing: 0.5px;
  }

  .headline {
    position: absolute; left: 237px; top: 18px;
    font-family: "Bebas Neue", sans-serif; font-size: 80px; line-height: 1;
    color: var(--white); white-space: nowrap; letter-spacing: 0.5px;
  }
  .headline__accent { color: var(--gold); }

  .subline {
    position: absolute; left: 244px; top: 98px;
    font-size: 49px; line-height: 1; color: var(--white);
    font-weight: 400; white-space: nowrap; letter-spacing: -0.5px;
  }
  .subline strong { font-weight: 700; }

  .office { position: absolute; left: 24px; top: 180px; line-height: 1.05; }
  .office__label { color: var(--gold); font-size: 18px; font-weight: 500; }
  .office__city { color: var(--ink); font-size: 26px; font-weight: 400; }
  .office__rule {
    position: absolute; left: 209px; top: 180px;
    width: 1.5px; height: 52px; background: var(--ink);
  }

  .website {
    position: absolute; left: 220px; top: 190px;
    font-size: 34px; font-weight: 600; color: var(--ink);
    white-space: nowrap; letter-spacing: -0.3px;
  }
</style>
</head>
<body>
  <section class="billboard">
    <svg class="billboard__shapes" width="900" height="262" viewBox="0 0 900 262">
      <defs>
        <linearGradient id="photoTone" x1="0" y1="0" x2="1" y2="1">
          <stop offset="0" stop-color="var(--photo-dark)"/>
          <stop offset="0.45" stop-color="#4a4a52"/>
          <stop offset="0.7" stop-color="var(--photo-light)"/>
          <stop offset="1" stop-color="#bfb8b0"/>
        </linearGradient>
      </defs>
      <rect class="band-navy" x="0" y="0" width="900" height="163" fill="var(--navy)"/>
      <path class="band-gold" d="M198 163 L246 101 L830 101 L830 171 L486 171 L474 163 Z" fill="var(--gold)"/>
      <path d="M772 134 Q820 94 900 88" fill="none" stroke="var(--navy)" stroke-width="14"/>
      <path d="M780 140 Q826 102 900 96" fill="none" stroke="var(--white)" stroke-width="4"/>
      <path role="img" aria-label="Photo of the attorney in a dark suit beside divorce papers and wedding rings"
            d="M685 262 L690 176 Q700 158 730 150 L760 150 Q790 104 900 99 L900 262 Z"
            fill="url(#photoTone)"/>
    </svg>

    <div class="brand">
      <div class="brand__dot"></div>
      <div class="brand__name">Harborline<br>Family Counsel</div>
    </div>

    <h1 class="headline">We charge a <span class="headline__accent">fixed fee</span></h1>
    <p class="subline">ON YOUR <strong>DIVORCE</strong></p>

    <div class="office">
      <div class="office__label">Main Office</div>
      <div class="office__city">Jacksonville</div>
    </div>
    <div class="office__rule"></div>
    <p class="website">www.steadyratesplit.com</p>
  </section>
</body>
</html>
```